Email design required

We need a design for a paid B2B email campaign and facebook / retargeting banner ads that match the same style.

Website: http://pelmora.staging.hostvantry.com/
Campaign Name: KEX Weariness
Example: http://liftmarrowsites.com/kex-weariness/
- I made this over the weekend. It has the right words, but the style / layout needs to change

Size: 600 pixels wide, no limit on length

Formatting:
Format CSS inline only - This will ensure that size, font family, colour, line height, etc. will all remain the same once it is dropped into our newsletter sending software. See below as an

example,

Here's a mockup of

Target Market(s)

Canadian mortgage brokers

Industry/Entity Type

Campaign

Font styles to use
Sans Serif

Colors
3277b5

Requirements
Must have
• Text from my website example http://liftmarrowsites.com/kex-weariness/
• Otherwise, do whatever you think would look good.

```html
<!DOCTYPE html>
<html lang="en">
<head>
<meta charset="utf-8">
<title>Pelmora – KEX Weariness Email</title>
<link href="https://fonts.googleapis.com/css2?family=Open+Sans:ital,wght@0,400;0,600;0,700;1,400&display=swap" rel="stylesheet">
<style>
  :root {
    --brand-blue: #3277b5;
    --logo-blue: #1f6fb8;
    --orange: #f7931e;
    --headline: #6b5b5b;
    --body-text: #5a5a5a;
    --muted: #777777;
    --row-light: #e4f0fa;
    --row-mid: #d5e9f8;
    --footer: #3e3b4a;
    --page-bg: #2e2e2e;
    --white: #ffffff;
  }
  * { box-sizing: border-box; margin: 0; padding: 0; }
  html, body { width: 960px; height: 1200px; overflow: hidden; }
  body { background: var(--page-bg); font-family: "Open Sans", Arial, sans-serif; color: var(--body-text); }

  .email { position: absolute; left: 180px; top: 5px; width: 600px; height: 1190px; background: var(--white); }

  .hero { position: relative; height: 332px; background: linear-gradient(180deg, #d7e8f7 0%, #e6f1fb 60%, #eef5fc 100%); }
  .brand { position: absolute; left: 26px; top: 22px; display: flex; align-items: center; gap: 6px; color: var(--logo-blue); font-weight: 600; font-size: 25px; line-height: 1; }
  .brand-square { width: 18px; height: 18px; background: var(--logo-blue); }
  .contact-link { position: absolute; right: 35px; top: 30px; font-size: 14px; color: var(--muted); text-decoration: none; }
  .hero-title { position: absolute; top: 80px; left: 0; right: 0; text-align: center; font-size: 36px; font-weight: 700; color: var(--headline); }
  .hero-offer { position: absolute; left: 22px; width: 300px; top: 173px; text-align: center; font-size: 14.5px; line-height: 20px; color: var(--body-text); }
  .hero-offer .price { color: var(--orange); }
  .hero-button { position: absolute; left: 71px; top: 237px; width: 180px; height: 43px; border-radius: 22px; background: var(--orange); color: var(--white); font-weight: 700; font-size: 14.5px; display: flex; align-items: center; justify-content: center; letter-spacing: .3px; }
  .hero-illustration { position: absolute; left: 342px; top: 154px; width: 180px; height: 144px; border-radius: 10px; background: linear-gradient(135deg, #f7a23c, #f08a14); }

  .section-band { position: relative; margin: 0 -2px; height: 49px; background: var(--brand-blue); color: var(--white); font-weight: 700; font-size: 17px; display: flex; align-items: center; justify-content: center; }

  .review { position: relative; height: 169px; }
  .review-avatar { position: absolute; left: 59px; top: 18px; width: 124px; height: 124px; border-radius: 50%; background: #555555; }
  .review-quote { position: absolute; left: 246px; top: 29px; width: 320px; font-size: 13px; line-height: 20px; font-style: italic; color: var(--muted); }
  .review-author { position: absolute; left: 246px; top: 115px; font-size: 13px; color: var(--muted); letter-spacing: .3px; }

  .compare { position: relative; height: 390px; }
  .compare-brand { position: absolute; left: 289px; top: 28px; display: flex; align-items: center; gap: 5px; color: var(--logo-blue); font-weight: 600; font-size: 21px; line-height: 1; }
  .compare-brand .brand-square { width: 15px; height: 15px; }
  .compare-rival { position: absolute; left: 450px; top: 32px; font-size: 14.5px; font-weight: 700; color: #111; }
  .compare-table { position: absolute; left: 41px; top: 74px; width: 504px; border-collapse: collapse; font-size: 13px; color: #333; }
  .compare-table td { height: 34px; vertical-align: middle; }
  .compare-table tr:nth-child(odd) { background: var(--row-light); }
  .compare-table tr:nth-child(even) { background: var(--row-mid); }
  .compare-table .icon-cell { width: 33px; text-align: center; }
  .compare-table .label-cell { width: 212px; }
  .compare-table .ours { width: 130px; text-align: center; font-weight: 700; }
  .compare-table .theirs { text-align: center; }
  .compare-table tr.tall td { vertical-align: top; padding-top: 9px; height: 101px; }
  .service-list { display: block; margin-top: 5px; font-style: italic; font-size: 12.5px; line-height: 21px; letter-spacing: -.3px; }
  .cta-button { position: absolute; left: 140px; top: 295px; width: 318px; height: 76px; border-radius: 38px; background: var(--orange); color: var(--white); text-align: center; font-weight: 700; }
  .cta-main { display: block; margin-top: 11px; font-size: 23px; letter-spacing: .8px; line-height: 30px; }
  .cta-sub { display: block; font-size: 14px; letter-spacing: .4px; }

  .about { height: 107px; padding: 13px 41px 0; font-size: 13px; line-height: 20px; color: var(--muted); }
  .footer { margin: 0 -1px; height: 46px; background: var(--footer); color: var(--white); font-size: 13px; display: flex; align-items: center; justify-content: space-between; padding: 0 32px 0 29px; }
</style>
</head>
<body>
  <main class="email">
    <header class="hero">
      <div class="brand"><span class="brand-square"></span>Pelmora</div>
      <a class="contact-link" href="#">Contact</a>
      <h1 class="hero-title">Experiencing KEX Weariness?</h1>
      <p class="hero-offer">Unlimited Notice of Assessment Orders<br>For Just <span class="price">$29 / Month</span></p>
      <div class="hero-button">Get Started Now</div>
      <div class="hero-illustration" role="img" aria-label="Illustration of a tired person slumped over a desk in an office chair"></div>
    </header>

    <h2 class="section-band">Customer Reviews</h2>
    <section class="review">
      <div class="review-avatar" role="img" aria-label="Customer avatar silhouette"></div>
      <p class="review-quote">I've used a few different services for this and Pelmora is by far the best. Fraction of the cost and I have the required docs within a couple of hours at most. Makes my life so much easier.</p>
      <p class="review-author">Marek Tolliver, Northgate Lending, Calgary</p>
    </section>

    <h2 class="section-band">Compare KEX Services</h2>
    <section class="compare">
      <div class="compare-brand"><span class="brand-square"></span>Pelmora</div>
      <div class="compare-rival">‘Other Guys’</div>
      <table class="compare-table">
        <tr>
          <td class="icon-cell"><svg width="14" height="14" viewBox="0 0 14 14"><circle cx="7" cy="7" r="5.5" fill="none" stroke="#999" stroke-width="1.5"/><path d="M4.5 7l2 2 5-5" fill="none" stroke="#999" stroke-width="1.6"/></svg></td>
          <td class="label-cell">Price</td><td class="ours">$29 / month</td><td class="theirs">$39 / Order</td>
        </tr>
        <tr>
          <td class="icon-cell"><svg width="14" height="14" viewBox="0 0 14 14"><circle cx="7" cy="7" r="5.5" fill="none" stroke="#999" stroke-width="1.5"/><path d="M4.5 7l2 2 5-5" fill="none" stroke="#999" stroke-width="1.6"/></svg></td>
          <td class="label-cell">Units</td><td class="ours">Unlimited</td><td class="theirs">Just One</td>
        </tr>
        <tr>
          <td class="icon-cell"><svg width="14" height="14" viewBox="0 0 14 14"><circle cx="7" cy="7" r="5.5" fill="none" stroke="#999" stroke-width="1.5"/><path d="M4.5 7l2 2 5-5" fill="none" stroke="#999" stroke-width="1.6"/></svg></td>
          <td class="label-cell">Turnaround</td><td class="ours">4 Hours</td><td class="theirs">1 Day</td>
        </tr>
        <tr class="tall">
          <td class="icon-cell"><svg width="14" height="14" viewBox="0 0 14 14"><circle cx="7" cy="7" r="5.5" fill="none" stroke="#999" stroke-width="1.5"/><path d="M4.5 7l2 2 5-5" fill="none" stroke="#999" stroke-width="1.6"/></svg></td>
          <td class="label-cell">Other Services<span class="service-list">Document Sorting, Lender Fulfillment, Closing Package Preparation, And Much More</span></td>
          <td class="ours"><svg width="22" height="18" viewBox="0 0 22 18"><rect x="1" y="3" width="14" height="14" fill="none" stroke="#3a4a5a" stroke-width="2"/><path d="M4 9l4 4 12-12" fill="none" stroke="#2cb5a0" stroke-width="3"/></svg></td>
          <td class="theirs">X</td>
        </tr>
      </table>
      <div class="cta-button"><span class="cta-main">GET STARTED NOW</span><span class="cta-sub">30-Day Money Back Guarantee</span></div>
    </section>

    <h2 class="section-band">About Us</h2>
    <p class="about">Pelmora provides on-demand administrative support for Mortgage Professionals across Canada. Everything from Notice of Assessment and Title Orders to inbound document sorting and lender fulfilment can be outsouced at a fraction of the cost of a full time administrator.</p>

    <footer class="footer"><span>© Pelmora 2016 All rights reserved.</span><span>Unsubscribe here</span></footer>
  </main>
</body>
</html>
```